Maplecrest Disability - Social Security Disability Attorneys

Our company is expanding to attract clients nationwide for our social security disability practice. We have a logo, but I am looking for a creative and elegant letterhead that projects an image of being technologically advanced but still professional enough for the legal field. I am looking for the "wow factor" combined with this is still professional enough for a law practice.

Requesting letterhead and business card design
Updates

Had to update and change the logo. The previous logo had a typo. Please send updates with the new logo for consideration. The letterhead and business cards should be professional enough to be used for a law firm. Thanks.

Industry/Entity Type

Law Practice, Law Firm, Healthcare Industry, Government

Colors

Designer to choose colors to be used in the design.

Requirements
Nice to have
• **Please create a vertical design for the business card**

```html
<!DOCTYPE html>
<html lang="en">
<head>
<meta charset="utf-8">
<title>Maplecrest Disability – Business Card</title>
<link href="https://fonts.googleapis.com/css2?family=Montserrat:wght@500;700&display=swap" rel="stylesheet">
<style>
  :root{
    --stage:#229ed9;
    --card-back:#5470b8;
    --card-front:#ffffff;
    --brand-blue:#5470b8;
    --accent:#f08228;
    --ink:#1d1d1d;
    --white:#ffffff;
  }
  html,body{margin:0;padding:0;overflow:hidden;}
  body{width:1200px;height:1128px;background:var(--stage);position:relative;font-family:"Montserrat",sans-serif;}
  .card{position:absolute;top:129px;width:500px;height:868px;border-radius:38px;overflow:hidden;text-align:center;}
  .card--back{left:70px;background:var(--card-back);color:var(--white);}
  .card--front{left:632px;width:497px;background:var(--card-front);color:var(--ink);}

  .brand{position:absolute;left:0;right:0;display:flex;align-items:center;justify-content:center;gap:12px;}
  .brand-mark{flex:none;width:14px;height:14px;border-radius:50%;background:var(--accent);}
  .brand-name{font-family:"Montserrat",sans-serif;font-weight:500;font-size:28px;letter-spacing:0.5px;margin:0;white-space:nowrap;}
  .card--back .brand{top:530px;}
  .card--back .brand-name{color:var(--white);}
  .card--front .brand{top:280px;}
  .card--front .brand-name{color:var(--brand-blue);}

  .industry{position:absolute;left:0;right:0;top:702px;font-size:20px;font-weight:500;line-height:31px;margin:0;}

  .person{position:absolute;left:0;right:0;top:308px;}
  .person-name{font-size:28px;font-weight:700;color:var(--accent);margin:0;letter-spacing:0.3px;}
  .person-role{display:flex;align-items:center;justify-content:center;gap:6px;font-size:22px;font-weight:500;margin:4px 0 0;}
  .person-role::before,.person-role::after{content:"";width:66px;height:2px;background:var(--accent);}

  .address{position:absolute;left:0;right:0;top:446px;font-size:19.5px;font-weight:500;line-height:29px;margin:0;}
  .contact-icons{position:absolute;left:0;right:0;top:560px;display:flex;justify-content:center;gap:34px;}
  .contact-icons svg{width:22px;height:22px;fill:var(--accent);}
  .contacts{position:absolute;left:0;right:0;top:606px;list-style:none;margin:0;padding:0;font-size:19.5px;font-weight:500;line-height:32.5px;}

  .footer-band{position:absolute;left:0;right:0;bottom:0;height:26px;background:var(--accent);}
</style>
</head>
<body>
  <section class="card card--back">
    <div class="brand">
      <span class="brand-mark"></span>
      <p class="brand-name">Maplecrest Disability</p>
    </div>
    <p class="industry">Law Practice, Law Firm,<br>Healthcare Industry, Government</p>
  </section>

  <section class="card card--front">
    <div class="brand">
      <span class="brand-mark"></span>
      <p class="brand-name">Maplecrest Disability</p>
    </div>
    <div class="person">
      <p class="person-name">DANIEL WHITCOMBE</p>
      <p class="person-role">Co-Founder</p>
    </div>
    <p class="address">Suite 4, Level 18, Harbour Lane<br>Sydney NSW 2000</p>
    <div class="contact-icons">
      <svg viewBox="0 0 24 24" aria-label="Phone"><path d="M6.6 10.8a15 15 0 0 0 6.6 6.6l2.2-2.2c.3-.3.7-.4 1-.2 1.1.4 2.3.6 3.6.6.6 0 1 .4 1 1V20c0 .6-.4 1-1 1A17 17 0 0 1 3 4c0-.6.4-1 1-1h3.5c.6 0 1 .4 1 1 0 1.3.2 2.5.6 3.6.1.3 0 .7-.2 1z"/></svg>
      <svg viewBox="0 0 24 24" aria-label="Email"><path d="M2 5h20v14H2z"/><path d="M2 5l10 8 10-8" fill="none" stroke="#fff" stroke-width="1.6"/></svg>
      <svg viewBox="0 0 24 24" aria-label="Website"><circle cx="12" cy="12" r="10"/><path d="M2 12h20M12 2c3 3 3 17 0 20M12 2c-3 3-3 17 0 20" fill="none" stroke="#fff" stroke-width="1.3"/></svg>
    </div>
    <ul class="contacts">
      <li>555-214-7390</li>
      <li>Info@maplecrestdisability.com</li>
      <li>www.maplecrestdisability.com</li>
    </ul>
    <div class="footer-band"></div>
  </section>
</body>
</html>
```